Top Pour Web site design

The aim of Top Pour is to provide an online service which allows customers to pre-order drinks and gain incentives such as fast entry, special offers (drinks, entry fees), as well as allowing customers to compare drinking establishments based upon costs and ratings.

what is required is the design of the pages stated below completed to the specifications.

Target Market(s)

The target market of Top Pour is men and women between the ages of 18 to 26 mainly. Within the age range of 18 to 26 the more specific target groups

Industry/Entity Type

Online

Requirements
Must have
• What is required to be designed

Website to be viewable on different systems e.g desktop, laptop and for mobile devices a mobile friendly page

Home page

Logo
Company name
Log in
Sign up
Help
Social media links, Follow us link

Bar, pub, club search function
Search by postcode, establishment type, distance

Pictorial instructions of how to use the site like ( quick dine). The stages are 1) select location 2) build order and pay 3) pick up from bar

Pre load results of establishments

Drinking establishment sign up

Map showing search results

List of results

My basket window which shows your order

Pop out box for customer sign up

Buttons for FAQ, general information, company information, Privacy policy ect at bottom of page

The home page is required to be Clear, simple, easy to use and stylish but not over the top with to much information which will confuse the customers. The preloaded results need to be obvious and where can be seen. The pictorial instructions should go below the preloaded results. Once the search criteria has been filled in and has been submitted the preloaded results and pictorial instructions will be removed and be replaced by the map and search results.

Drinking establishment personal page requires

Details of drinking establishment (name, address, contact, map)
list of drinks avliable
My basket
Special Offers
Gallery
Calendar
Reviews section at the bottom

When a person clicks on a drinking establishment page what that person should see when they open the page is company name logo
with a list of the drinks they offer and special offers. Tabs or buttons for gallery, establishment details, calender and special offers should be located along top or down the left. when they are clicked on they will replace the menu.

The colour scheme is based around the logo which is attached. We do not want any pink or overly bright colours which would not go with the logo.

A site which we like is this one
http://www.quick-dine.example.co.uk/
this site is perfect simple, clear but also good looking. If you need inspiration you should use this site as a starting point.
Should not have
• what should be avoided is a site which like this one http://platepoint.example.co.uk/~beta/?gclid=XQMWpLaRtnfGDsHYbTqeKZPLv

it is to complicated with bad font and colours. The site just feels cheesy and not classy. we like very little about this site

```html
<!DOCTYPE html>
<html lang="en">
<head>
<meta charset="utf-8">
<title>Top Pour – Order your round online</title>
<link rel="stylesheet" href="https://fonts.googleapis.com/css2?family=Cabin+Sketch:wght@400;700&family=Open+Sans:wght@400;600;700&display=swap">
<style>
:root{
  --brand:#2e3192;
  --brand-light:#5b5fd6;
  --ink:#333333;
  --muted:#666666;
  --grey:#c9c9c9;
  --line:#bdbdbd;
  --paper:#ffffff;
  --fog:#e4e4e4;
}
*{box-sizing:border-box;margin:0;padding:0}
html,body{width:1187px;height:1200px;overflow:hidden}
body{
  position:relative;
  font-family:"Open Sans",Arial,sans-serif;
  color:var(--ink);
  background:linear-gradient(to bottom,#fff 0,#fff 680px,var(--fog) 1080px);
  border-top:4px solid #c8c8c8;
}
.abs{position:absolute}

/* header */
.brand{left:184px;top:30px;display:flex;align-items:center;gap:10px}
.brand-mark{width:54px;height:54px;border-radius:50%;border:5px solid #9a9a9a}
.brand-name{font-size:29px;font-weight:600;color:var(--brand)}
.social{display:flex;gap:5px}
.social span{width:22px;height:22px;border-radius:50%;background:var(--brand);display:block}
.social.top{left:902px;top:22px}
.cart{left:551px;top:61px;font-size:12.5px;color:var(--muted);display:flex;align-items:center;gap:6px}
.cart b{color:#2952d9;font-weight:700}
.cart .btn{border:1px solid #aaa;background:#e6e6e6;padding:2px 9px;color:#444;margin-left:4px}
.account{left:816px;top:60px;font-size:14.5px;font-weight:600;color:#444}
.help{left:927px;top:58px;border:1px solid #bbb;border-radius:5px;padding:2px 9px;font-size:12px;color:var(--brand);background:#fff;box-shadow:0 1px 2px rgba(0,0,0,.2)}

/* search banner */
.search{left:184px;top:127px;width:820px;height:127px;background:var(--brand)}
.search h1{position:absolute;left:50px;top:18px;font-family:"Cabin Sketch",cursive;font-weight:700;font-size:38px;color:#fff;letter-spacing:.5px}
.field{position:absolute;top:72px;height:31px;background:#fff;border:1px solid #ccc;font-size:14px;color:#555;padding:5px 9px;font-family:Arial,sans-serif}
.field.select::after{content:"";position:absolute;right:8px;top:13px;border:4px solid transparent;border-top:5px solid #333}
.search-btn{position:absolute;left:581px;top:72px;width:155px;height:32px;background:linear-gradient(#6d71e6,#3e42b8);border:1px solid #9ea0ee;color:#fff;font-weight:700;font-size:16px;display:flex;align-items:center;justify-content:center;gap:6px;box-shadow:0 2px 3px rgba(0,0,0,.35)}

/* listings */
.section-title{font-family:"Cabin Sketch",cursive;font-weight:700;font-size:39px;color:#444}
.venue{width:380px;height:104px;border-bottom:1px dashed var(--line)}
.thumb{position:absolute;left:0;top:0;width:78px;height:78px;box-shadow:1px 2px 3px rgba(0,0,0,.4)}
.venue h2{position:absolute;left:88px;top:-5px;font-size:17px;font-weight:700;color:var(--brand)}
.venue dl{position:absolute;left:88px;top:20px;font-size:12px;line-height:20px;display:grid;grid-template-columns:91px auto}
.venue dt{font-weight:700;color:#444}
.venue dd{color:#555}
.venue dd.cost{color:var(--brand)}
.rating{position:absolute;left:250px;top:60px;font-size:12px;font-weight:700;color:#444;display:flex;align-items:center;gap:6px}
.rating i{display:block;width:12px;height:11px;border-radius:2px;background:var(--grey)}
.rating i.on{background:var(--brand-light)}

/* how it works */
.how-title{left:0;width:1187px;top:720px;text-align:center;font-family:"Cabin Sketch",cursive;font-weight:700;font-size:40px;color:var(--brand)}
.step{width:258px;height:188px;background:var(--paper);box-shadow:0 10px 8px -4px rgba(0,0,0,.3);transform:rotate(-.6deg)}
.step .tape{position:absolute;left:88px;top:-14px;width:96px;height:26px;background:rgba(190,190,190,.6)}
.step .num{position:absolute;left:30px;top:16px;width:27px;height:32px;border-radius:50%;background:var(--brand);color:#fff;font-family:"Cabin Sketch",cursive;font-weight:700;font-size:20px;display:flex;align-items:center;justify-content:center}
.step .art{position:absolute;left:66px;top:35px;width:126px;height:90px;border-radius:10px}
.step p{position:absolute;left:0;right:0;top:136px;text-align:center;font-family:"Cabin Sketch",cursive;font-weight:700;font-size:20px;color:#555}
.arrow{width:70px;height:40px}

/* footer */
.footer{left:0;top:1081px;width:1187px;height:119px;background:var(--brand)}
.footer nav{position:absolute;left:179px;top:41px;font-size:13px;color:#fff}
.footer nav a{color:#fff;text-decoration:none}
.footer small{position:absolute;left:179px;top:61px;font-size:13px;color:#b7b8e8}
.social.bottom{position:absolute;left:895px;top:45px}
.social.bottom span{background:#fff}
</style>
</head>
<body>

<header>
  <div class="abs brand"><span class="brand-mark"></span><span class="brand-name">Top Pour</span></div>
  <div class="abs social top" aria-label="Follow us"><span></span><span></span><span></span><span></span></div>
  <div class="abs cart">
    <svg width="14" height="12" viewBox="0 0 14 12"><path d="M0 1h3l2 7h7l2-5H4" fill="none" stroke="#444" stroke-width="1.6"/><circle cx="6" cy="10.5" r="1.3" fill="#444"/><circle cx="11" cy="10.5" r="1.3" fill="#444"/></svg>
    <span><b>0</b> items | Subtotal : <b>$0.0</b></span><span class="btn">Checkout</span>
  </div>
  <div class="abs account">Log in . Sign up</div>
  <div class="abs help">NEED HELP</div>
</header>

<section class="abs search">
  <h1>Order your round online</h1>
  <div class="field" style="left:52px;width:182px">Your Postcode</div>
  <div class="field select" style="left:222px;width:162px">Establishment Type</div>
  <div class="field select" style="left:401px;width:162px">Distance</div>
  <div class="search-btn">SEARCH NOW
    <svg width="16" height="16" viewBox="0 0 16 16"><circle cx="6.5" cy="6.5" r="5" fill="none" stroke="#fff" stroke-width="2"/><path d="M10 10l5 5" stroke="#fff" stroke-width="2.4"/></svg>
  </div>
</section>

<h2 class="abs section-title" style="left:183px;top:280px">Drinking establishment</h2>

<section>
  <article class="abs venue" style="left:184px;top:343px">
    <div class="thumb" role="img" aria-label="Photo of The Lantern pub front" style="background:linear-gradient(#8a7b6a,#2d2a27)"></div>
    <h2>The LANTERN</h2>
    <dl><dt>Provides</dt><dd>: Food &amp; Drink</dd><dt>Special offers</dt><dd>: 15% Off</dd><dt>Cost</dt><dd class="cost">: £5.00</dd></dl>
    <div class="rating">Rating <i class="on"></i><i class="on"></i><i class="on"></i><i></i><i></i></div>
  </article>
  <article class="abs venue" style="left:618px;top:343px">
    <div class="thumb" role="img" aria-label="Photo of Harbour Arms building" style="background:linear-gradient(#d9dbe0,#6d6e6a)"></div>
    <h2>HARBOUR ARMS</h2>
    <dl><dt>Provides</dt><dd>: Food &amp; Drink</dd><dt>Special offers</dt><dd>: 20% Off</dd><dt>Cost</dt><dd class="cost">: £2.00</dd></dl>
    <div class="rating">Rating <i class="on"></i><i class="on"></i><i class="on"></i><i class="on"></i><i class="on"></i></div>
  </article>
  <article class="abs venue" style="left:184px;top:463px">
    <div class="thumb" role="img" aria-label="Photo of Bell &amp; Compass pub front" style="background:linear-gradient(#4d5a7a,#1e1e1e)"></div>
    <h2>BELL &amp; COMPASS</h2>
    <dl><dt>Provides</dt><dd>: Food &amp; Drink</dd><dt>Special offers</dt><dd>: 10% Off</dd><dt>Cost</dt><dd class="cost">: £3.00</dd></dl>
    <div class="rating">Rating <i class="on"></i><i></i><i></i><i></i><i></i></div>
  </article>
  <article class="abs venue" style="left:618px;top:463px">
    <div class="thumb" role="img" aria-label="Photo of live music at The Wexley" style="background:linear-gradient(#b06f7e,#2b1214)"></div>
    <h2>THE WEXLEY</h2>
    <dl><dt>Provides</dt><dd>: Food &amp; Drink</dd><dt>Special offers</dt><dd>: 10% Off</dd><dt>Cost</dt><dd class="cost">: £3.00</dd></dl>
    <div class="rating">Rating <i class="on"></i><i class="on"></i><i class="on"></i><i></i><i></i></div>
  </article>
  <article class="abs venue" style="left:184px;top:583px">
    <div class="thumb" role="img" aria-label="Photo of a band on stage at Fiddlebox" style="background:linear-gradient(#c65a86,#1c0d16)"></div>
    <h2>FIDDLEBOX</h2>
    <dl><dt>Provides</dt><dd>: Food &amp; Drink</dd><dt>Special offers</dt><dd>: 20% Off</dd><dt>Cost</dt><dd class="cost">: £2.00</dd></dl>
    <div class="rating">Rating <i class="on"></i><i class="on"></i><i class="on"></i><i></i><i></i></div>
  </article>
  <article class="abs venue" style="left:618px;top:583px">
    <div class="thumb" role="img" aria-label="Photo of Marquis of Fenwick pub front" style="background:linear-gradient(#6b6a66,#22252b)"></div>
    <h2>MARQUIS OF FENWICK</h2>
    <dl><dt>Provides</dt><dd>: Food &amp; Drink</dd><dt>Special offers</dt><dd>: 5% Off</dd><dt>Cost</dt><dd class="cost">: £3.00</dd></dl>
    <div class="rating">Rating <i class="on"></i><i class="on"></i><i class="on"></i><i class="on"></i><i></i></div>
  </article>
</section>

<section>
  <h2 class="abs how-title">How it Works</h2>
  <div class="abs step" style="left:178px;top:810px">
    <span class="tape"></span><span class="num">1</span>
    <div class="art" role="img" aria-label="Illustration of a map with a magnifying glass" style="background:linear-gradient(135deg,#7fc4e8,#5aa64a 60%,#c7622c)"></div>
    <p>Select Location</p>
  </div>
  <div class="abs step" style="left:462px;top:810px">
    <span class="tape"></span><span class="num">2</span>
    <div class="art" role="img" aria-label="Illustration of a cash register" style="background:linear-gradient(#f2d06b,#c9cfd8 55%,#a7b2c0)"></div>
    <p>build order and pay</p>
  </div>
  <div class="abs step" style="left:747px;top:810px">
    <span class="tape"></span><span class="num">3</span>
    <div class="art" role="img" aria-label="Illustration of two glasses of red wine" style="background:linear-gradient(#fff,#b0244f 45%,#e9e9e9)"></div>
    <p>pick up from bar</p>
  </div>
  <svg class="abs arrow" style="left:388px;top:872px" viewBox="0 0 70 40"><path d="M2 10 Q35 -6 65 28" fill="none" stroke="#888" stroke-width="1.6"/><path d="M58 26l7 3 0-8" fill="none" stroke="#888" stroke-width="1.6"/></svg>
  <svg class="abs arrow" style="left:674px;top:872px" viewBox="0 0 70 40"><path d="M2 10 Q35 -6 65 28" fill="none" stroke="#888" stroke-width="1.6"/><path d="M58 26l7 3 0-8" fill="none" stroke="#888" stroke-width="1.6"/></svg>
</section>

<footer class="abs footer">
  <nav><a href="#">FAQ</a> | <a href="#">general information</a> | <a href="#">company information</a> | <a href="#">Privacy policy</a></nav>
  <small>Copyright © 2013 Top Pour. All rights reserved</small>
  <div class="social bottom" aria-label="Follow us"><span></span><span></span><span></span><span></span></div>
</footer>

</body>
</html>
```